Coastal Learner Bureau business cards

Australian company about to start offering its services. We recruit international students to come to study English, vocational education and postgraduate courses in Australia. We help them find the institution and select the right city they want to come to Australia. We are a young, online oriented and supportive agency. Our clients are between 18 and 35 years old, mainly University students, young professionals or people with work experience. We provide much more information that any other agency offer. We administrate a Facebook group with more than 11.000 members that daily ask questions about general information when coming to Australia, while they are here and even after they leave the country

Target Market(s)

International students from South America, Central America and Europe

Industry/Entity Type

Student

Contact Information for Business Card

Tomas Bilbrea
Managing Director
tomas@kelvarin.com.au
www.kelvoria.com.au
+61 491058264
Melbourne, Australia

Font styles to use
Serif
Sans Serif

Colors

Designer to choose colors to be used in the design.

Requirements
Must have
• Horizontal design
• Standard business card size and shape. If font uses green or yellow colours, they will have to match the ones from the logo
Nice to have
• UPDATE: Use the contents of the green image to design one of the card sides. Use our logo in the background of that side as watermark.
• Passport image, or immigration stamps. A picture of the Yarra River (from Melbourne) would be cool as well.
Should not have
• Non-standard business card size and shape
• Not black as the background colour of any sides as we are not a VIP agency or a hight class service. We are orientes to young people and they like colours, pictures, something attractive.
• Vertical design
• NO YELLOW or BLACK AS THE BACKGROUND COLOUR OF ANY SIDE OF THE BIZ CARD

```html
<!DOCTYPE html>
<html lang="en">
<head>
<meta charset="utf-8">
<title>Kelvoria business cards</title>
<link rel="stylesheet" href="https://fonts.googleapis.com/css2?family=Open+Sans:wght@400;700&display=swap">
<style>
  :root {
    --stage: #111111;
    --paper: #fbf9f3;
    --green: #0d6e4a;
    --yellow: #eec91b;
    --white: #ffffff;
  }
  * { box-sizing: border-box; margin: 0; padding: 0; }
  html, body { width: 1200px; height: 1000px; overflow: hidden; background: var(--stage); }
  body { font-family: "Open Sans", Arial, sans-serif; }
  .stage {
    position: relative; width: 1200px; height: 1000px;
    display: flex; align-items: center; justify-content: center; gap: 40px;
  }
  .card {
    width: 520px; height: 297px; background: var(--paper);
    position: relative; box-shadow: 0 8px 24px rgba(0,0,0,.5);
  }
  /* front */
  .card--front { display: flex; align-items: center; justify-content: center; gap: 14px; }
  .brand-dot { width: 22px; height: 22px; border-radius: 50%; background: var(--yellow); }
  .brand-name { color: var(--green); font-weight: 700; font-size: 46px; letter-spacing: .5px; }
  /* back */
  .card--back { padding: 16px; }
  .back-panel { position: relative; width: 100%; height: 100%; background: var(--green); overflow: hidden; }
  .name-band {
    height: 40%; background: var(--yellow);
    padding: 18px 0 0 22px;
  }
  .person-name { color: var(--green); font-weight: 700; font-size: 19px; }
  .role { position: absolute; left: 22px; top: 46%; color: var(--white); font-size: 13px; }
  .contact-list { position: absolute; left: 22px; top: 63%; list-style: none; }
  .contact-list li { display: flex; align-items: center; gap: 8px; color: var(--yellow); font-size: 13px; line-height: 19px; }
  .contact-list svg { width: 12px; height: 12px; fill: var(--white); flex: none; }
  .location {
    position: absolute; right: 22px; bottom: 16px; text-align: right;
    color: var(--white); font-size: 15px; line-height: 19px;
  }
</style>
</head>
<body>
<main class="stage">
  <section class="card card--front" aria-label="Card front">
    <span class="brand-dot"></span>
    <span class="brand-name">Kelvoria</span>
  </section>

  <section class="card card--back" aria-label="Card back">
    <div class="back-panel">
      <div class="name-band"><h1 class="person-name">Tomas Bilbrea</h1></div>
      <p class="role">Managing Director</p>
      <ul class="contact-list">
        <li><svg viewBox="0 0 24 24"><path d="M6.6 10.8a15.1 15.1 0 0 0 6.6 6.6l2.2-2.2a1 1 0 0 1 1-.25 11.4 11.4 0 0 0 3.6.57 1 1 0 0 1 1 1V20a1 1 0 0 1-1 1A17 17 0 0 1 3 4a1 1 0 0 1 1-1h3.5a1 1 0 0 1 1 1c0 1.25.2 2.45.57 3.57a1 1 0 0 1-.25 1z"/></svg>+61 49 10 58 264</li>
        <li><svg viewBox="0 0 24 24"><path d="M2 5h20v14H2z M2 5l10 8 10-8" fill="none" stroke="#fff" stroke-width="2.4"/></svg>tomas@kelvarin.com.au</li>
        <li><svg viewBox="0 0 24 24"><circle cx="12" cy="12" r="10" fill="none" stroke="#fff" stroke-width="2.2"/><path d="M2 12h20M12 2c3 3 3 17 0 20M12 2c-3 3-3 17 0 20" fill="none" stroke="#fff" stroke-width="2"/></svg>www.kelvoria.com.au</li>
      </ul>
      <p class="location">Melbourne<br>Australia</p>
    </div>
  </section>
</main>
</body>
</html>
```